Calvanto Group Real Estate Company business cards

New business card design, we are generally happy with the basic layout of the existing front of business card, (feel free to change) but require a head shot photo on the back side.

http://www.calvanto.com.au/

Attached logos, and existing business card

------------------------------

Target Market(s)

Real estate

Industry/Entity Type

Real Estate

Contact Information for Business Card

Standard size double sided

Font styles to use
Other font styles liked:
• Futura

Requirements
Must have
• Photo head shot on the back side
Nice to have
• yes
Should not have
• No

```html
<!DOCTYPE html>
<html lang="en">
<head>
<meta charset="utf-8">
<title>Calvanto Group business cards</title>
<link rel="stylesheet" href="https://fonts.googleapis.com/css2?family=Libre+Baskerville:wght@400;700&display=swap">
<style>
  :root {
    --backdrop: #2a2a2a;
    --card-white: #ffffff;
    --card-shade: #ececee;
    --brand-purple: #2f2466;
    --brand-orange: #e8891c;
    --contact-text: #ffffff;
    --photo-light: #c9ccd6;
    --photo-dark: #2b3350;
  }
  * { margin: 0; padding: 0; box-sizing: border-box; }
  html, body {
    width: 1200px; height: 873px; overflow: hidden;
    background: var(--backdrop);
    font-family: "Libre Baskerville", "Times New Roman", serif;
  }
  .canvas {
    position: relative; width: 1200px; height: 873px;
  }
  .card {
    position: absolute; top: 277px;
    width: 520px; height: 318px;
    border-radius: 18px; overflow: hidden;
    background: linear-gradient(180deg, var(--card-white) 0%, var(--card-shade) 100%);
  }
  .card--front { left: 60px; }
  .card--back { left: 620px; }

  .brand-name {
    position: absolute;
    color: var(--brand-purple);
    font-weight: 400;
    letter-spacing: 0.5px;
    white-space: nowrap;
  }
  .card--front .brand-name { left: 0; right: 0; top: 110px; text-align: center; font-size: 40px; }

  .service-band {
    position: absolute; left: 0; right: 0; top: 168px; height: 40px;
    background: var(--brand-purple);
    display: flex; justify-content: center; align-items: center; gap: 26px;
  }
  .service-band span {
    color: var(--brand-orange); font-size: 18px; letter-spacing: 1px;
  }

  .card--back .brand-name { left: 30px; top: 64px; font-size: 29px; letter-spacing: 0; }
  .agent-name {
    position: absolute; left: 34px; top: 126px;
    color: var(--brand-orange); font-size: 21px;
  }
  .agent-role {
    position: absolute; left: 34px; top: 156px;
    color: var(--brand-purple); font-size: 13px; font-weight: 700;
  }
  .skyline {
    position: absolute; left: 0; right: 0; top: 196px; bottom: 0;
    background: var(--brand-purple);
  }
  .headshot {
    position: absolute; right: 26px; top: 22px; bottom: 0; width: 180px;
    background: linear-gradient(180deg, var(--photo-light) 0%, var(--photo-dark) 60%);
  }
  .contact-list {
    position: absolute; left: 34px; bottom: 22px; list-style: none;
  }
  .contact-list li {
    display: flex; align-items: center; gap: 10px;
    color: var(--contact-text); font-size: 13px; line-height: 22px;
  }
  .contact-list svg { width: 12px; height: 12px; flex: none; }
</style>
</head>
<body>
<main class="canvas">
  <section class="card card--front" aria-label="Card front">
    <div class="brand-name">Calvanto Group</div>
    <div class="service-band">
      <span>BUY</span><span>SELL</span><span>RENT</span>
    </div>
  </section>

  <section class="card card--back" aria-label="Card back">
    <div class="skyline" role="img" aria-label="City skyline silhouette in brand purple"></div>
    <div class="headshot" role="img" aria-label="Head shot photo of the director in a navy suit"></div>
    <div class="brand-name">Calvanto Group</div>
    <div class="agent-name">Daniel Tran</div>
    <div class="agent-role">Director</div>
    <ul class="contact-list">
      <li>
        <svg viewBox="0 0 12 12" aria-hidden="true"><rect x="3" y="0.5" width="6" height="11" rx="1.2" fill="none" stroke="var(--brand-orange)" stroke-width="1.3"/><circle cx="6" cy="9.5" r="0.8" fill="var(--brand-orange)"/></svg>
        0412-508-316
      </li>
      <li>
        <svg viewBox="0 0 12 12" aria-hidden="true"><rect x="0.5" y="2.5" width="11" height="7" fill="var(--brand-orange)"/><path d="M0.5 2.5 L6 6.5 L11.5 2.5" fill="none" stroke="var(--brand-purple)" stroke-width="1"/></svg>
        daniel.tran@calvanto.com.au
      </li>
      <li>
        <svg viewBox="0 0 12 12" aria-hidden="true"><circle cx="6" cy="6" r="5" fill="none" stroke="var(--brand-orange)" stroke-width="1.2"/><ellipse cx="6" cy="6" rx="2.2" ry="5" fill="none" stroke="var(--brand-orange)" stroke-width="1"/><line x1="1" y1="6" x2="11" y2="6" stroke="var(--brand-orange)" stroke-width="1"/></svg>
        www.calvanto.com.au
      </li>
    </ul>
  </section>
</main>
</body>
</html>
```